Web Design job - Condo Debts Collection Business needs a Web Design

I need a site for a client, who works with condo debts collection, and ensure all revenues provided by condo fees will be always available to the building manager of condo on a specific date, regardless of defaults.
I have the visual identity (logo, slogan and colors) of the company, and some requirements on layout (kind of slider, menu options, phone number on a noble position, etc) - maybe I can do a sketch, but I like the idea of give some freedom to designer.

*** PLEASE, we have no interest in templates. We want something new***

Target Market(s)

I have two targets for this design: - Condominium's building manager. This target is looking for a solution to overdue debts on it's condo. - Residents on condominiums. This target wants to live in a better place, where their neighbors pay their condominium fees on time.

Number of Pages Required

1 page

Requirements
Must have
• - Slider with title, some short text related, a nice image (I prefer happy and/or peaceful family, people doing business, happy friends, and so on).
• - I have a special attention to menu. I'm looking for one I can have a nice effect, more elegant, charming, kind of innovative.
• - Phone number on the top (or clearly visible).
• - Member log in area or icon on the top (or clearly visible).
• - News/articles area.
• - Modern fonts, with good quality, sans-serif on areas where reading is more intensive (prefer Google web-fonts).
• - Colors specified on attached files.
Nice to have
• - Clear background color, cause it's better to read larger texts (like articles). Dark backgrounds makes reading difficult.
• - A site with effects (like shadows, lines, curves, gradients, lights) is usually pretty.
• - I pay attention on beautiful footers.
Should not have
• - Images with a lot of money (I don't sell richness, I sell tranquility, peace, harmony, safety).
• - Poor menu.

```html
<!DOCTYPE html>
<html lang="en">
<head>
<meta charset="utf-8">
<title>Zelmorin – Condo Fee Collection</title>
<link href="https://fonts.googleapis.com/css2?family=Open+Sans:wght@300;400;600;700&display=swap" rel="stylesheet">
<style>
:root{
  --gold:#e2a923;
  --gold-deep:#c6982f;
  --gold-light:#e8b93a;
  --ink:#231f20;
  --text:#2b2b2b;
  --page:#f6f6f6;
  --rule:#cfcfcf;
  --white:#ffffff;
}
*{margin:0;padding:0;box-sizing:border-box}
html,body{width:735px;height:1200px;overflow:hidden}
body{background:var(--page);font-family:"Open Sans",Arial,sans-serif;color:var(--text);position:relative}
.abs{position:absolute}

/* header */
.brand{left:26px;top:22px;display:flex;align-items:center;gap:10px}
.brand-mark{width:28px;height:28px;background:var(--gold)}
.brand-name{font-size:34px;font-weight:700;color:var(--ink);letter-spacing:-0.5px;line-height:1}
.phone{left:472px;top:18px;display:flex;align-items:center;gap:8px;font-size:19px;color:var(--ink)}
.login{left:658px;top:21px;width:58px;height:21px;border:2px solid var(--gold);color:var(--gold);font-size:13px;font-weight:600;display:flex;align-items:center;justify-content:center;text-decoration:none}

/* hero */
.hero{left:0;top:94px;width:735px;height:407px}
.hero-title{left:0;top:244px;width:735px;text-align:center;color:var(--white);font-size:42px;font-weight:700;letter-spacing:0.5px}
.hero-sub{left:0;top:293px;width:735px;text-align:center;color:var(--white);font-size:20px;font-weight:600}
.hero-btn{left:295px;top:355px;width:144px;height:34px;border:1.5px solid var(--white);color:var(--white);font-size:13px;font-weight:600;display:flex;align-items:center;justify-content:center}
.dots{left:332px;top:459px;display:flex;gap:16px}
.dot{width:12px;height:12px;border-radius:50%;background:#e9e9e9}
.dot.is-active{background:var(--gold-light)}

/* nav */
.main-nav{left:138px;top:81px;width:464px;height:32px}
.nav-links{left:138px;top:81px;width:464px;height:32px;display:flex;align-items:center;font-size:13.5px;font-weight:600;color:var(--white)}
.nav-links span{position:absolute}

/* section headings */
.section-title{left:0;width:735px;text-align:center;font-size:28px;font-weight:300;color:var(--ink)}
.section-title .accent{color:var(--gold);font-weight:700}
.rule{left:114px;width:536px;height:1.5px;background:var(--rule)}
.rule-accent{left:291px;width:179px;height:1.5px;background:var(--gold)}
.intro{left:117px;top:607px;width:500px;text-align:center;font-size:13.5px;line-height:17.5px;color:var(--text)}

/* news */
.arrow{top:744px}
.card{width:160px}
.card-img{height:108px}
.card-date{font-size:10.5px;margin-top:8px;color:var(--ink)}
.card-text{font-size:10px;line-height:12.5px;margin-top:5px;color:#3a3a3a}
.card-btn{display:inline-block;margin-top:10px;background:var(--gold-deep);color:var(--white);font-size:10px;padding:4px 6px}

/* footer */
.footer{left:0;top:1012px;width:735px;height:188px;background:var(--ink);color:var(--white)}
.foot-head{font-size:13px;top:1035px}
.foot-list{top:1068px;font-size:13px;line-height:17.3px}
.map{left:517px;top:1071px;width:121px;height:81px}
.foot-rule{left:0;top:1162px;width:735px;height:1px;background:#5a5657}
.foot-rule-accent{left:245px;top:1162px;width:247px;height:1px;background:var(--gold)}
.legal{top:1173px;font-size:10.5px;color:var(--white)}
</style>
</head>
<body>

<header>
  <div class="abs brand"><span class="brand-mark"></span><span class="brand-name">zelmorin</span></div>
  <div class="abs phone">
    <svg width="18" height="18" viewBox="0 0 24 24"><path fill="#e2a923" d="M6.6 10.8a15.5 15.5 0 0 0 6.6 6.6l2.2-2.2c.3-.3.7-.4 1-.2 1.1.4 2.3.6 3.6.6.6 0 1 .4 1 1V20c0 .6-.4 1-1 1A17 17 0 0 1 3 4c0-.6.4-1 1-1h3.5c.6 0 1 .4 1 1 0 1.3.2 2.5.6 3.6.1.3 0 .7-.2 1z"/></svg>
    <span>(020) 5550 1948</span>
  </div>
  <a class="abs login" href="#">LOGIN</a>
</header>

<section class="hero-area">
  <svg class="abs hero" viewBox="0 0 735 407" role="img" aria-label="Photo of a smiling young man using a tablet outdoors among green trees">
    <defs>
      <linearGradient id="heroFill" x1="0" y1="0" x2="1" y2="1">
        <stop offset="0" stop-color="#5d6b40"/>
        <stop offset="0.45" stop-color="#6f7a5a"/>
        <stop offset="0.75" stop-color="#4a5138"/>
        <stop offset="1" stop-color="#2b2d22"/>
      </linearGradient>
    </defs>
    <polygon points="0,0 735,0 735,344 367,406 0,344" fill="url(#heroFill)"/>
    <polygon points="0,0 735,0 735,344 367,406 0,344" fill="#000" opacity="0.18"/>
  </svg>
  <div class="abs hero-title">WELCOME TO ZELMORIN</div>
  <div class="abs hero-sub">Your number one debt collector</div>
  <div class="abs hero-btn">LEARN MORE</div>
  <div class="abs dots"><span class="dot is-active"></span><span class="dot"></span><span class="dot"></span></div>
</section>

<nav>
  <svg class="abs main-nav" viewBox="0 0 464 32">
    <defs>
      <linearGradient id="navDark" x1="0" y1="0" x2="1" y2="0">
        <stop offset="0" stop-color="#2a2a2a"/><stop offset="1" stop-color="#5e5e5e"/>
      </linearGradient>
      <linearGradient id="navGold" x1="0" y1="0" x2="1" y2="0">
        <stop offset="0" stop-color="#d7a93a"/><stop offset="0.6" stop-color="#caa04a"/><stop offset="1" stop-color="#e3b43c"/>
      </linearGradient>
    </defs>
    <polygon points="0,0 98,0 112,32 10,32" fill="url(#navDark)"/>
    <polygon points="98,0 452,0 464,32 112,32" fill="url(#navGold)"/>
  </svg>
  <div class="abs nav-links">
    <span style="left:43px">HOME</span>
    <span style="left:127px">ABOUT US</span>
    <span style="left:227px">OUR SERVICES</span>
    <span style="left:361px">NEWS</span>
  </div>
</nav>

<section class="welcome">
  <h1 class="abs section-title" style="top:548px">WELCOME TO <span class="accent">zelmorin</span></h1>
  <div class="abs rule" style="top:595px"></div>
  <div class="abs rule-accent" style="top:595px"></div>
  <p class="abs intro">Lorem ipsum dolor sit amet, consectetur adipiscing elit, sed do eiusmod tempor incididunt ut labore et dolore magna aliqua. Ut enim ad minim veniam, quis nostrud exercitation ullamco laboris nisi ut aliquip ex ea commodo consequat. Duis aute irure dolor in reprehenderit in voluptate</p>
</section>

<section class="news">
  <svg class="abs arrow" style="left:113px" width="12" height="18" viewBox="0 0 12 18"><polyline points="10,2 3,9 10,16" fill="none" stroke="#9a9a9a" stroke-width="3"/></svg>
  <svg class="abs arrow" style="left:635px" width="12" height="18" viewBox="0 0 12 18"><polyline points="2,2 9,9 2,16" fill="none" stroke="#9a9a9a" stroke-width="3"/></svg>
  <h2 class="abs section-title" style="top:733px">NEWS</h2>
  <div class="abs rule" style="top:779px"></div>
  <div class="abs rule-accent" style="top:779px"></div>

  <article class="abs card" style="left:114px;top:801px">
    <div class="card-img" role="img" aria-label="Photo of a happy family relaxing together on a bed" style="background:linear-gradient(160deg,#3f6a66,#b98f74 55%,#d9d6d2)"></div>
    <div class="card-date">POSTED ON 04-07-2018</div>
    <div class="card-text">Lorem ipsum dolor sit amet, con-<br>sectetur adipiscing elit, sed do</div>
    <span class="card-btn">READ MORE</span>
  </article>
  <article class="abs card" style="left:301px;top:801px">
    <div class="card-img" role="img" aria-label="Photo of a handshake in front of a suburban house" style="background:linear-gradient(180deg,#9fb7cf,#b7ad9a 45%,#4c5a3e 80%,#3b3b3b)"></div>
    <div class="card-date">POSTED ON 04-07-2018</div>
    <div class="card-text">Lorem ipsum dolor sit amet, con-<br>sectetur adipiscing elit, sed do</div>
    <span class="card-btn">READ MORE</span>
  </article>
  <article class="abs card" style="left:490px;top:801px">
    <div class="card-img" role="img" aria-label="Photo of a happy family relaxing together on a bed" style="background:linear-gradient(160deg,#3f6a66,#b98f74 55%,#d9d6d2)"></div>
    <div class="card-date">POSTED ON 04-07-2018</div>
    <div class="card-text">Lorem ipsum dolor sit amet, con-<br>sectetur adipiscing elit, sed do</div>
    <span class="card-btn">READ MORE</span>
  </article>
</section>

<footer>
  <div class="abs footer"></div>
  <div class="abs foot-head" style="left:67px;color:#fff">QUICK LINKS</div>
  <div class="abs foot-head" style="left:240px;color:#fff">CONTACT US</div>
  <div class="abs foot-head" style="left:516px;color:#fff">LOCATION MAP</div>
  <ul class="abs foot-list" style="left:67px;list-style:none;color:#fff">
    <li>Home</li><li>About Us</li><li>Services</li><li>News</li>
  </ul>
  <div class="abs foot-list" style="left:240px;color:#fff">
    Email: hello@zelmorin-mail.com<br>Tel: (020) 5550 1948<br>Street: Example qyv, Home Town
  </div>
  <div class="abs map" role="img" aria-label="Street map showing the office location" style="background:linear-gradient(120deg,#8fb8e0 0%,#cfd6dc 30%,#e4e2dc 70%,#d9dccf 100%)"></div>
  <div class="abs foot-rule"></div>
  <div class="abs foot-rule-accent"></div>
  <div class="abs legal" style="left:15px">Copyright © 2018 Northgate Studio. All rights reserved</div>
  <div class="abs legal" style="left:566px">Terms Of Service | Privacy Policy</div>
</footer>

</body>
</html>
```